Label design for organic saffron, saffron and herbal syrup

We cultivate saffron, Damszen roses, flowers and herbs. We would need a recognizable outfit (label) for our products. Theoretically (and practically) we have "converted" the family coat of arms into a kind of LOGO. I would send this in the attachment. It would be nice if - in one way or another - this LOGO / coat of arms could be used (certainly with other colors). For some time we have played with the idea of changing the second part of the family name "Wallmoser" (in German .... greuth sounds similar to Kraut / herb [English]) .... eg Wallmoser's saffron syrup into the labeling.
Our products are primarily syrups, currently herbal syrup and saffron syrup. Here the first problem arises, the only bottles / caps that are actually approved for syrup filling (hot filling) are appallingly ugly (see attachment), the only possibility of "sprucing up" is to use so-called "shrink sleeves" (here we need a diameter of 31 and a length of about 40), the colors of which are also limited. Besides the syrup, we sell saffron as a spice and various herbal mixtures (see appendix current packaging saffron). Our quantities are small (syrup 200ml-330ml), saffron in the gram range.
We also need quasi the back of the labeling (this should be able to be redefined per charge) .... Batch 1 (with small quantity has eg more of herb xy than the next batch or the saffron syrup with batch xy needs more / less saffron). In addition, we are certified organic (for this reason, the reverse side would also have to contain all the requirements of organic labeling) [see attachment].
We do not really want to address a specific clientele. Maybe just people who want to taste, enjoy, mix drinks, cook .... (and - unfortunately - don't like Corvel syrup :-) and want to pay a bit more, or find our saffron or herbs better than others) .
In summary
- Strong recognition value (possibly inclusion of "coat of arms", color variable ... although I personally don't like yellow that much)
- Saffron syrup (the color of the saffron syrup is yellow / golden-yellow-light orange, in a transparent ugly bottle)
- Herbal syrup (color variable from blue / green / brown / red elements, in transparent ugly bottle)
Saffron and other herbs (very small containers, type of container not yet fixed)
Regarding a potential "style" I can unfortunately give little information. On the one hand, I am in love with minimalism, on the other hand, I find the translucent, cryptic, implied enormously attractive and sometimes even the "overloaded" colorful has its charm. I think that all in all, it just has to be coherent, and then it will be good.
Requirements
Must have
- Integration of Code of Arms, modifiable for different products

```html
<!DOCTYPE html>
<html lang="de">
<head>
<meta charset="utf-8">
<title>Wallmoser Rose Sirup – Label</title>
<link rel="stylesheet" href="https://fonts.googleapis.com/css2?family=Noto+Serif:wght@600;700&family=Open+Sans:wght@700&display=swap">
<style>
  :root {
    --plum: #7c1b4f;
    --plum-deep: #5e1039;
    --gold: #d9b453;
    --gold-light: #f1d98c;
    --cream: #fdf0c9;
    --ink: #262626;
    --navy: #2a2a6a;
    --crest-tone: #c9cde6;
    --badge-green: #4aa64a;
    --badge-pale: #c8e29c;
    --paper: #ffffff;
  }
  html, body {
    margin: 0;
    padding: 0;
    width: 809px;
    height: 1200px;
    overflow: hidden;
    background: var(--paper);
  }
  .label {
    position: relative;
    width: 809px;
    height: 1200px;
  }
  .label-shapes {
    position: absolute;
    inset: 0;
  }
  .brand-name {
    position: absolute;
    left: 236px;
    width: 308px;
    top: 318px;
    margin: 0;
    text-align: center;
    font-family: "Noto Serif", serif;
    font-weight: 600;
    font-size: 46px;
    color: var(--navy);
  }
  .product-title {
    position: absolute;
    left: 216px;
    width: 341px;
    top: 548px;
    margin: 0;
    text-align: center;
    font-family: "Noto Serif", serif;
    font-weight: 700;
    font-size: 74px;
    line-height: 84px;
    color: var(--paper);
    -webkit-text-stroke: 3px var(--ink);
    paint-order: stroke fill;
  }
  .vertical-copy {
    position: absolute;
    writing-mode: vertical-rl;
    transform: rotate(180deg);
    font-family: "Open Sans", sans-serif;
    font-weight: 700;
    color: var(--ink);
    margin: 0;
  }
  .ingredients {
    left: 72px;
    top: 512px;
    height: 536px;
    font-size: 14px;
    line-height: 18px;
    letter-spacing: 0.5px;
    text-align: center;
  }
  .producer {
    left: 643px;
    top: 510px;
    height: 342px;
    font-size: 12.6px;
    line-height: 16px;
    letter-spacing: 0.55px;
    text-align: start;
  }
  .producer-line {
    display: block;
  }
  .producer-note {
    margin-block-end: 8px;
  }
  .best-before {
    left: 641px;
    top: 893px;
    width: 72px;
    height: 162px;
    box-sizing: border-box;
    border: 1.5px solid var(--ink);
    background: var(--paper);
    font-size: 15px;
    line-height: 20px;
    letter-spacing: 1px;
    padding-top: 10px;
    padding-right: 8px;
  }
  .volume, .dilution {
    position: absolute;
    top: 1066px;
    margin: 0;
    font-family: "Open Sans", sans-serif;
    font-weight: 700;
    font-size: 17px;
    color: var(--ink);
  }
  .volume { left: 274px; }
  .dilution { left: 447px; }
</style>
</head>
<body>
<main class="label">
  <svg class="label-shapes" width="809" height="1200" viewBox="0 0 809 1200">
    <defs>
      <linearGradient id="pattern-tone" x1="0" y1="0" x2="1" y2="1">
        <stop offset="0" stop-color="#8a2458"/>
        <stop offset="0.45" stop-color="#9a4a5a"/>
        <stop offset="0.75" stop-color="#7c1b4f"/>
        <stop offset="1" stop-color="#93405a"/>
      </linearGradient>
      <linearGradient id="gold-bar" x1="0" y1="0" x2="0" y2="1">
        <stop offset="0" stop-color="#f1d98c"/>
        <stop offset="0.5" stop-color="#d9b453"/>
        <stop offset="1" stop-color="#b98f2f"/>
      </linearGradient>
      <clipPath id="header-clip">
        <rect x="38" y="36" width="707" height="379"/>
      </clipPath>
    </defs>

    <rect class="label-ground" x="38" y="36" width="707" height="1086" fill="var(--cream)"/>

    <rect class="header-ornament" x="38" y="36" width="707" height="379" fill="url(#pattern-tone)"
          role="img" aria-label="Gold lace paisley ornament on plum background"/>

    <g class="emblem-medallion" clip-path="url(#header-clip)">
      <circle cx="370" cy="246" r="186" fill="var(--paper)" stroke="var(--gold)" stroke-width="4"/>
      <rect x="326" y="30" width="126" height="90" fill="var(--paper)"/>
    </g>
    <line x1="324" y1="36" x2="324" y2="86" stroke="var(--gold)" stroke-width="3"/>
    <line x1="454" y1="36" x2="454" y2="86" stroke="var(--gold)" stroke-width="3"/>

    <rect class="crest-placeholder" x="330" y="176" width="120" height="120" fill="var(--crest-tone)"
          role="img" aria-label="Family coat of arms emblem"/>

    <rect class="gold-divider" x="38" y="416" width="707" height="24" fill="url(#gold-bar)"/>
    <ellipse cx="38" cy="428" rx="5" ry="12" fill="#c9a241"/>
    <ellipse cx="745" cy="428" rx="5" ry="12" fill="#c9a241"/>

    <path class="product-panel" d="M217 440 H556 V664 A169.5 169.5 0 0 1 217 664 Z"
          fill="var(--plum)" stroke="var(--gold)" stroke-width="4"
          role="img" aria-label="Faint line drawing of a rose on plum panel"/>

    <g class="organic-badge">
      <rect x="352" y="940" width="76" height="146" fill="var(--badge-pale)" stroke="var(--badge-green)" stroke-width="1.5"/>
      <rect x="356" y="946" width="68" height="46" fill="var(--paper)"/>
      <circle cx="390" cy="969" r="18" fill="var(--badge-green)"/>
      <rect x="358" y="996" width="64" height="44" fill="var(--badge-green)"/>
    </g>
  </svg>

  <p class="brand-name">Wallmoser</p>

  <h1 class="product-title">Rose<br>Sirup</h1>

  <p class="vertical-copy ingredients">ZUTATEN: Lorem ipsum dolor sit amet, consectetur adipiscing elit.<br>Morbi ultricies molestie orci. Aenean purus mauris, sodales nec<br>diam dignissim, porttitor laoreet enim. Aliquam id sollicitudin<br>turpis. Vivamus aliquet elit sem, et ornare ex aliquam in.</p>

  <div class="vertical-copy producer">
    <span class="producer-line producer-note">*aus kontrolliert biologischer Landwirtschaft</span>
    <span class="producer-line">Expertly crafted by: Harlan-Wallmoser</span>
    <span class="producer-line">1234 Street Name, Any City, District, Country</span>
  </div>

  <p class="vertical-copy best-before">Best Before:</p>

  <p class="volume">330mL</p>
  <p class="dilution">1:7</p>
</main>
</body>
</html>
```